Harrow Tavern & Grille Menu Makeover

I am looking for a professional look to update our current menu. We are an independently owned sports bar and grill. Up to this point, I have done all of my own graphic designing. I am looking for something classy/family oriented. We are a very family friendly sports bar that offers a wide variety of menu options. Our website is www.harrowtavernco.example. This may help you get more of a feel for what type of place we are and what we offer. Our menu is listed on the website. My current menu is 8.5x14 inserts that feature a cover page, 4 inside pages and a back page. I would like something a little more condensed than this. Possibly a large tri-fold menu? I am open to all new ideas. I do have some pictures on my menu now, and would like to continue using a few pictures to feature some of my items. I would like something that is in a format that gives me the option to change items and prices on my own in the future. I would also like it to feature, or inform my patrons about our technology that we offer. We offer online ordering and we are a "verified venue" with Brewvoke.( a social site for craft beer lovers).

Industry/Entity Type

Sports Bar

Requirements
Nice to have
• Nice to have some pictures, but does not have to. We do feature 9 different beers on tap. A lot of them are local craft beers from the state of Kansas. Not sure if that is something we can feature, but it is a nice talking point. All of our tables and bar are hand built. With a rich mahogany finish on all of our woodwork, some type of "woodgrain" look into the menu would be nice.

```html
<!DOCTYPE html>
<html lang="en">
<head>
<meta charset="utf-8">
<title>Harrow Tavern &amp; Grille — Appetizers &amp; Salads</title>
<link rel="stylesheet" href="https://fonts.googleapis.com/css2?family=Cinzel:wght@700&family=Playfair+Display:wght@500&family=Bebas+Neue&display=swap">
<style>
  :root {
    --wood-dark: #4a1a0e;
    --wood-mid: #7a3220;
    --wood-light: #8e4026;
    --ink: #24180e;
    --ink-soft: #3a2a1a;
    --photo-app: #b9a24a;
    --photo-salad: #5c6a2a;
    --frame: #2a140a;
  }
  * { margin: 0; padding: 0; box-sizing: border-box; }
  html, body { width: 850px; height: 1200px; overflow: hidden; }
  body {
    position: relative;
    background:
      linear-gradient(90deg, rgba(0,0,0,.18), rgba(0,0,0,0) 20%, rgba(0,0,0,0) 80%, rgba(0,0,0,.2)),
      linear-gradient(180deg, var(--wood-mid), var(--wood-light) 45%, var(--wood-dark));
    color: var(--ink);
    font-family: "Bebas Neue", "Arial Narrow", sans-serif;
  }
  .layer { position: absolute; left: 0; top: 0; }
  .brand-name {
    position: absolute; top: 64px; left: 0; width: 850px; text-align: center;
    font-family: "Cinzel", "Times New Roman", serif; font-weight: 700;
    font-size: 52px; line-height: 60px; letter-spacing: 15px; padding-left: 15px; color: #160c06;
  }
  .brand-sub {
    position: absolute; top: 126px; left: 0; width: 850px; text-align: center;
    font-family: "Cinzel", "Times New Roman", serif; font-weight: 700;
    font-size: 21px; line-height: 26px; letter-spacing: 1px; color: #160c06;
  }
  .photo { position: absolute; border-radius: 50%; border: 4px solid var(--frame); }
  .photo-appetizer {
    left: 644px; top: 176px; width: 156px; height: 156px;
    background: radial-gradient(circle at 55% 40%, #e8e2c8 0 12%, var(--photo-app) 32%, #6d7a30 66%, #1b1a12);
  }
  .photo-salad {
    left: 706px; top: 712px; width: 108px; height: 108px;
    background: radial-gradient(circle at 45% 50%, #c24a2c 0 15%, var(--photo-salad) 45%, #2f3a18 80%, #1d160c);
  }
  .section-title {
    position: absolute; left: 94px;
    font-family: "Playfair Display", Georgia, serif; font-weight: 500;
    font-size: 36px; line-height: 40px; color: var(--ink);
  }
  .title-appetizers { top: 302px; }
  .title-salads { top: 760px; }
  .item { position: absolute; }
  .col-left { left: 98px; width: 318px; }
  .col-right { left: 427px; width: 330px; }
  .item-name {
    font-family: "Bebas Neue", "Arial Narrow", sans-serif; font-weight: 400;
    font-size: 17px; line-height: 17px; color: var(--ink);
  }
  .item-desc {
    font-family: "Bebas Neue", "Arial Narrow", sans-serif; font-weight: 400;
    font-size: 10.5px; line-height: 12px; color: var(--ink-soft);
  }
  .item-price {
    font-family: "Bebas Neue", "Arial Narrow", sans-serif; font-weight: 400;
    font-size: 7px; line-height: 9px; letter-spacing: .5px; color: var(--ink-soft);
  }
</style>
</head>
<body>
  <svg class="layer" width="850" height="1200" viewBox="0 0 850 1200" aria-hidden="true">
    <defs>
      <radialGradient id="paper" cx="50%" cy="50%" r="65%">
        <stop offset="0%" stop-color="#dcc59d"/>
        <stop offset="70%" stop-color="#c6a777"/>
        <stop offset="100%" stop-color="#8f6c3e"/>
      </radialGradient>
    </defs>
    <g stroke="#160c06" stroke-width="1.6" fill="#160c06">
      <line x1="216" y1="60" x2="632" y2="60"/>
      <circle cx="216" cy="60" r="2.5"/><circle cx="632" cy="60" r="2.5"/>
      <line x1="292" y1="169" x2="560" y2="169"/>
      <circle cx="292" cy="169" r="2.5"/><circle cx="560" cy="169" r="2.5"/>
    </g>
    <polygon fill="url(#paper)" points="
      70,222 120,214 200,218 260,210 330,216 380,212 440,220 520,212 600,218 660,210 710,222 790,214
      796,260 800,330 790,380 798,470 792,540 800,620 792,690 802,760 792,820 798,900 790,980 800,1060 794,1126
      740,1132 680,1124 620,1134 540,1126 470,1136 400,1126 350,1112 300,1130 220,1124 150,1134 90,1126 50,1130
      44,1060 54,1000 40,940 52,880 44,820 38,760 50,700 40,640 54,580 42,520 52,460 36,400 48,340 40,280 58,240"/>
    <line x1="208" y1="734" x2="640" y2="734" stroke="#24180e" stroke-width="1.2"/>
  </svg>
  <svg class="layer" width="850" height="1200" viewBox="0 0 850 1200" role="img" aria-label="Decorative scroll flourishes">
    <ellipse cx="424" cy="51" rx="28" ry="6" fill="#160c06" opacity=".75"/>
    <ellipse cx="424" cy="174" rx="22" ry="5" fill="#160c06" opacity=".75"/>
    <ellipse cx="424" cy="734" rx="18" ry="6" fill="#24180e"/>
  </svg>

  <header>
    <div class="brand-name">HARROW</div>
    <div class="brand-sub">TAVERN &amp; GRILLE</div>
  </header>

  <div class="photo photo-appetizer" role="img" aria-label="Photo of crispy fried eggrolls around a cup of dipping sauce"></div>
  <div class="photo photo-salad" role="img" aria-label="Photo of a fresh berry salad with strawberries, blackberries and greens"></div>

  <h2 class="section-title title-appetizers">APPETIZERS</h2>

  <section class="appetizers">
    <article class="item col-left" style="top:354px"><h3 class="item-name">Slider Burgers</h3><p class="item-desc">Six juicy bite sized burgers topped with American cheese and served with pickle slices.</p><p class="item-price">8.99</p></article>
    <article class="item col-left" style="top:410px"><h3 class="item-name">Loaded Potato Skins</h3><p class="item-desc">Six crispy skins loaded with jack, cheddar and mozzarella cheese, then topped with smoked bacon and green onions. Served with sour cream.</p><p class="item-price">8.99</p></article>
    <article class="item col-left" style="top:466px"><h3 class="item-name">Rattlesnake Eggs</h3><p class="item-desc">A spicy combo of pepper jack cheese and jalapeños, battered and fried.</p><p class="item-price">7.99</p></article>
    <article class="item col-left" style="top:510px"><h3 class="item-name">Mozzarella Cheese Sticks</h3><p class="item-desc">Classic battered mozzarella cheese sticks served with ranch dressing.</p><p class="item-price">7.99</p></article>
    <article class="item col-left" style="top:554px"><h3 class="item-name">Grand Slam French Fries</h3><p class="item-desc">French fries loaded with jack, cheddar, mozzarella, bacon, jalapeños and green onions! Served with ranch dressing.</p><p class="item-price">7.99</p></article>
    <article class="item col-left" style="top:610px"><h3 class="item-name">Bang Bang Shrimp</h3><p class="item-desc">Lightly breaded and fried shrimp coated with a spicy Thai sauce, topped with parmesan cheese and diced tomatoes. Served over a bed of romaine lettuce.</p><p class="item-price">7.99</p></article>
    <article class="item col-left" style="top:666px"><h3 class="item-name">Ballpark Pretzel Basket</h3><p class="item-desc">Buttered and salted pretzels served with nacho cheese sauce.</p><p class="item-price">7.99</p></article>

    <article class="item col-right" style="top:354px"><h3 class="item-name">Spicy Southwest Chicken Eggrolls</h3><p class="item-desc">Stuffed with black beans, corn and chicken. Served with southwest ranch.</p><p class="item-price">9.99</p></article>
    <article class="item col-right" style="top:398px"><h3 class="item-name">Blooming Onion</h3><p class="item-desc">This fan favorite is classically carved and deep fried to perfection. Served with Harrow signature dipping sauce.</p><p class="item-price">7.99</p></article>
    <article class="item col-right" style="top:454px"><h3 class="item-name">Chicken Quesadilla</h3><p class="item-desc">A 12 inch flour tortilla stuffed with grilled chicken and jack and cheddar cheese. Served with salsa.</p><p class="item-price">8.99</p></article>
    <article class="item col-right" style="top:510px"><h3 class="item-name">Hank's Boneless Buffalo Wings</h3><p class="item-desc">A full pound of spicy, boneless buffalo wings. Served with ranch dressing or Hank's gold label sauce.</p><p class="item-price">7.99</p></article>
    <article class="item col-right" style="top:566px"><h3 class="item-name">Harrow Loaded Nachos</h3><p class="item-desc">Tri-colored tortilla chips smothered with creamy Monterey jack cheese, choice of beef or chicken, and topped with grilled peppers and onions, jalapeños and diced tomatoes. Served with sour cream and salsa.</p><p class="item-price">9.99</p></article>
    <article class="item col-right" style="top:634px"><h3 class="item-name">Garlic Bread Basket</h3><p class="item-desc">Tri-colored tortilla chips smothered with creamy Monterey jack cheese, choice of beef or chicken, and topped with grilled peppers and onions, jalapeños and diced tomatoes. Served with sour cream and salsa.</p><p class="item-price">9.99</p></article>
  </section>

  <h2 class="section-title title-salads">SALADS</h2>

  <section class="salads">
    <article class="item col-left" style="top:810px"><h3 class="item-name">Chicken Tender Garden Salad</h3><p class="item-desc">A spring lettuce mix topped with shredded jack and cheddar cheese, garden vegetables, bacon, croutons and egg. With your choice of crispy or grilled chicken.</p><p class="item-price">LARGE 8.99 / SMALL 7.99</p></article>
    <article class="item col-left" style="top:866px"><h3 class="item-name">Nacho Crispito Salad</h3><p class="item-desc">Harrow's unique blend of iceberg lettuce, topped with jack and cheddar cheese, tomatoes, black olives, ranch style beans and creamy Italian dressing. Topped with Crispito chips</p><p class="item-price">LARGE 8.99 / SMALL 7.99</p></article>
    <article class="item col-left" style="top:934px"><h3 class="item-name">Cobb Salad</h3><p class="item-desc">Rows of ham, turkey and roast beef, side by side with baby corn, jack and cheddar cheese, egg slices, garden vegetables, bacon and croutons served over iceberg lettuce.</p><p class="item-price">LARGE 8.99 / SMALL 7.99</p></article>
    <article class="item col-left" style="top:1002px"><h3 class="item-name">Summer Berry Salad</h3><p class="item-desc">A blend of fresh berries, tomatoes, croutons, mandarin oranges and crumbled feta cheese served on fresh spinach leaves. Your choice of chicken or shrimp.</p><p class="item-price">LARGE 8.99 / SMALL 7.99</p></article>

    <article class="item col-right" style="top:810px"><h3 class="item-name">House Caesar Salad</h3><p class="item-desc">A classic mix of crisp romaine lettuce, shredded parmesan cheese, and croutons. Served with our signature Caesar dressing.</p><p class="item-price">LARGE 6.99 / SMALL 5.99<br>LARGE WITH CHICKEN 8.99 / SMALL WITH CHICKEN 6.99</p></article>
    <article class="item col-right" style="top:874px"><h3 class="item-name">Nacho Crispito Salad</h3><p class="item-desc">Harrow's unique blend of iceberg lettuce, topped with jack and cheddar cheese, tomatoes, black olives, ranch style beans and creamy Italian dressing. Topped with Crispito chips.</p><p class="item-price">LARGE 8.99 / SMALL 7.99</p></article>
    <article class="item col-right" style="top:942px"><h3 class="item-name">Cobb Salad</h3><p class="item-desc">Rows of ham, turkey and roast beef, side by side with baby corn, jack and cheddar cheese, egg slices, garden vegetables, bacon and croutons served over iceberg lettuce.</p><p class="item-price">LARGE 8.99 / SMALL 7.99</p></article>
    <article class="item col-right" style="top:1010px"><h3 class="item-name">Summer Berry Salad</h3><p class="item-desc">A blend of fresh berries, tomatoes, croutons, mandarin oranges and crumbled feta cheese served on fresh spinach leaves. Your choice of chicken or shrimp.</p><p class="item-price">LARGE 8.99 / SMALL 7.99</p></article>
  </section>
</body>
</html>
```